To design a brand identity that is simple and creative with 'Corvane' as the brand name, I like modern simple fonts like helvetica neue, I want to print both sides of the card, I am open to dark front and white back, but the design needs to transfer well to letter heads and email signatures, I am looking for sophisticated and elegant, but open minded about clever and off the wall, I do not do 'boring' Corvane Ventures is the mother company for a small group, specialising in Management & consulting, Software development and construction, we have a high level of integrity, we are transparent and accountable for what we do. my images are provided as a guide only, Im not expecting them to be just copied, Im looking for a creator and passionate thinker, who will put life into their work.

Target Market(s)

usually business minded people who are looking for something different in me, such as leadership, confidence and focus with thinking that is per haps a little outside the box..

Industry/Entity Type

Construction

Requirements
Must have
• clean, minmalistic
Nice to have
• custom logo
Should not have
• boring, traditional

```html
<!DOCTYPE html>
<html lang="en">
<head>
<meta charset="utf-8">
<title>Corvane Ventures – Business Card</title>
<link href="https://fonts.googleapis.com/css2?family=Open+Sans:wght@400;700&display=swap" rel="stylesheet">
<style>
  :root {
    --page: #ece9e4;
    --card-dark: #1c1c1c;
    --card-dark-edge: #2e2e2e;
    --card-light: #ffffff;
    --brand-orange: #ec6a2c;
    --name-yellow: #f5b51c;
    --text-light: #e8e8e8;
    --text-grey: #8a8a8a;
    --service-red: #ea4a55;
    --bullet-grey: #9a9a9a;
    --url-dark: #333333;
    --band-warm: #f08a1e;
    --band-mid: #d3344a;
    --band-cool: #2a9d94;
  }
  * { box-sizing: border-box; margin: 0; padding: 0; }
  html, body { width: 1200px; height: 720px; overflow: hidden; }
  body {
    background: var(--page);
    font-family: "Open Sans", Helvetica, Arial, sans-serif;
    position: relative;
  }
  .card {
    position: absolute;
    width: 540px;
    height: 309px;
    top: 205px;
    border-radius: 4px;
    overflow: hidden;
    box-shadow: 0 6px 18px rgba(0,0,0,.18);
  }
  .card--front {
    left: 40px;
    background: linear-gradient(160deg, var(--card-dark-edge), var(--card-dark) 55%);
  }
  .card--back { left: 620px; background: var(--card-light); }

  .card__band {
    position: absolute; left: 0; right: 0; bottom: 0; height: 56px;
    background: linear-gradient(90deg, var(--band-warm), var(--band-mid) 50%, var(--band-cool));
  }

  .brand { position: absolute; display: flex; align-items: center; }
  .brand__dot { border-radius: 50%; background: var(--brand-orange); flex: none; }
  .brand__name {
    font-family: "Open Sans", Helvetica, Arial, sans-serif;
    font-weight: 400;
    color: var(--brand-orange);
    line-height: 1;
  }
  .tagline {
    position: absolute;
    color: var(--text-grey);
    font-size: 12px;
    letter-spacing: .5px;
  }

  .card--front .brand { left: 38px; top: 52px; gap: 14px; }
  .card--front .brand__dot { width: 40px; height: 40px; }
  .card--front .brand__name { font-size: 50px; }
  .card--front .tagline { left: 92px; top: 114px; }

  .holder {
    position: absolute; right: 298px; top: 152px;
    text-align: right; color: var(--text-light); font-size: 12px; line-height: 1.45;
  }
  .holder__name { color: var(--name-yellow); font-weight: 700; font-size: 17px; }
  .divider {
    position: absolute; left: 252px; top: 158px;
    width: 1px; height: 50px; background: var(--text-grey);
  }
  .contact {
    position: absolute; left: 262px; top: 154px;
    list-style: none; color: var(--text-light); font-size: 12px; line-height: 1.7;
  }
  .contact__item { display: flex; align-items: center; gap: 6px; }
  .contact__icon { width: 11px; height: 11px; fill: var(--name-yellow); }

  .card--back .brand { left: 52px; top: 62px; gap: 18px; }
  .card--back .brand__dot { width: 48px; height: 48px; }
  .card--back .brand__name { font-size: 60px; }
  .card--back .tagline { left: 118px; top: 136px; font-size: 13px; }

  .services {
    position: absolute; left: 90px; top: 178px; width: 380px;
    list-style: none; display: flex; flex-wrap: wrap; gap: 4px 14px;
    font-size: 12px; text-transform: uppercase; color: var(--service-red);
  }
  .services__item::before {
    content: ""; display: inline-block; width: 5px; height: 5px;
    border-radius: 50%; background: var(--bullet-grey);
    margin-right: 4px; vertical-align: middle;
  }
  .website {
    position: absolute; left: 220px; top: 238px;
    font-size: 16px; letter-spacing: 4px; color: var(--url-dark);
  }
</style>
</head>
<body>

<section class="card card--front" aria-label="Card front">
  <div class="card__band" role="img" aria-label="Decorative colour band in orange, red and teal"></div>

  <div class="brand">
    <span class="brand__dot"></span>
    <span class="brand__name">Corvane</span>
  </div>
  <p class="tagline">building what comes next</p>

  <div class="holder">
    <p class="holder__name">Your Name</p>
    <p class="holder__title">Title</p>
    <p class="holder__address">Po Box 418 Eastvale 6104</p>
  </div>
  <span class="divider"></span>
  <ul class="contact">
    <li class="contact__item">
      <svg class="contact__icon" viewBox="0 0 24 24" aria-hidden="true"><path d="M6.6 10.8a15.1 15.1 0 0 0 6.6 6.6l2.2-2.2a1 1 0 0 1 1-.25 11.4 11.4 0 0 0 3.6.57 1 1 0 0 1 1 1V20a1 1 0 0 1-1 1A17 17 0 0 1 3 4a1 1 0 0 1 1-1h3.5a1 1 0 0 1 1 1c0 1.25.2 2.45.57 3.57a1 1 0 0 1-.25 1z"/></svg>
      +61 0400 512 947
    </li>
    <li class="contact__item">
      <svg class="contact__icon" viewBox="0 0 24 24" aria-hidden="true"><path d="M2 5h20v14H2z M2 5l10 8 10-8" fill="none" stroke="var(--name-yellow)" stroke-width="2.5"/></svg>
      names@corvane.ventures
    </li>
  </ul>
</section>

<section class="card card--back" aria-label="Card back">
  <div class="brand">
    <span class="brand__dot"></span>
    <span class="brand__name">Corvane</span>
  </div>
  <p class="tagline">building what comes next</p>

  <ul class="services">
    <li class="services__item">Management &amp; Consulting</li>
    <li class="services__item">Software Development</li>
    <li class="services__item">Construction</li>
  </ul>
  <p class="website">www.corvane.com</p>
</section>

</body>
</html>
```